Healthcare website

We want to replace our website using joomla as the CMS. We want it to be device agnostic (gantry etc). Our business is health care our clients are people with high level spinal cord injuries ( quadriplegia / tetraplegia etc ). The site is a marketing tool primarily to potential clients and a portal for existing staff to access forms etc. It will showcase our key staff and our capability. It will also be where any new recruits apply to work with us. It must allow us to integrate our social media initiatives also. The final design must convey sophistication, high quality care and be warm and welcoming.

current web site is www.tendralwick.com.au
Updates

I have made small change to the brief in that i have removed the prefered color and indicated it would be nice to see some images that symbolize change / transformation like butterflies etc. thank you

Target Market(s)

Our business is health care our clients are people with high level spinal cord injuries ( quadriplegia / tetraplegia etc ).

Industry/Entity Type

Marketing

Colors

Designer to choose colors to be used in the design.

Requirements
Must have
• The site is a marketing tool primarily to potential clients and a portal for existing staff to access forms etc. It will showcase our key staff and our capability. It will also be where any new recruits apply to work with us. It must allow us to integrate our social media initiatives also. The final design must convey sophistication, high quality care and be warm and welcoming.
Nice to have
• Would be nice to incorporate images that symbolize change and new transformations - butterflies etc.

```html
<!DOCTYPE html>
<html lang="en">
<head>
<meta charset="utf-8">
<title>Tendralwick Care</title>
<link href="https://fonts.googleapis.com/css2?family=Open+Sans:wght@400;600;700&display=swap" rel="stylesheet">
<style>
:root{
  --page:#eef0f2;
  --white:#ffffff;
  --blue:#2a7fc6;
  --blue-dark:#1b5f9c;
  --navy:#143a61;
  --orange:#f08a1c;
  --ink:#333c44;
  --muted:#7a8590;
  --line:#dde2e7;
  --footer:#262b30;
  --footer-bar:#1b1f23;
  --footer-text:#aab3bb;
}
*{box-sizing:border-box;margin:0;padding:0}
html,body{width:814px;height:1200px;overflow:hidden}
body{background:var(--page);font-family:"Open Sans",Arial,sans-serif;color:var(--ink);font-size:9px;line-height:1.5}
.site{position:relative;width:814px;height:1200px;background:var(--white)}
.wrap{position:absolute;left:82px;width:654px}

/* header */
.header{top:0;height:95px}
.brand{position:absolute;left:0;top:32px}
.brand-name{font-size:20px;font-weight:600;color:var(--ink)}
.appointment{position:absolute;right:0;top:30px;text-align:right}
.appointment small{display:block;font-size:9px;color:var(--muted)}
.appointment strong{font-size:17px;color:var(--blue);font-weight:700}

/* nav */
.nav{position:absolute;left:0;top:95px;width:814px;height:28px;background:linear-gradient(var(--blue),var(--blue-dark))}
.nav ul{position:absolute;left:82px;list-style:none;display:flex;height:28px}
.nav li{color:var(--white);font-size:9px;font-weight:600;padding:0 16px;line-height:28px;border-right:1px solid rgba(255,255,255,.25)}
.nav li.active{background:rgba(0,0,0,.15)}

/* hero */
.hero{top:128px;height:282px;border-radius:2px;overflow:hidden}
.hero-photo{position:absolute;inset:0;background:linear-gradient(100deg,#d9e3ea 0%,#c7d4de 40%,#e9ecef 70%,#b8c6d2 100%)}
.hero-caption{position:absolute;left:60px;top:180px;width:340px;padding:10px 14px;background:rgba(20,58,97,.85);border-radius:3px}
.hero-caption p{color:var(--white);font-size:12px}
.hero-caption h2{color:var(--orange);font-size:18px;font-weight:700;white-space:nowrap}
.hero-dots{position:absolute;bottom:10px;left:50%;transform:translateX(-50%);display:flex;gap:5px}
.hero-dots span{width:7px;height:7px;border-radius:50%;background:rgba(255,255,255,.6)}
.hero-dots span.on{background:var(--blue)}

/* features */
.features{top:428px;height:210px;display:flex;gap:20px}
.feature{flex:1}
.feature-photo{height:110px;border-radius:2px}
.feature h3{font-size:14px;color:var(--blue);font-weight:600;margin:8px 0 4px}
.feature p{color:var(--muted)}
.btn{display:inline-block;margin-top:6px;background:var(--blue);color:var(--white);font-size:7px;font-weight:700;padding:3px 8px;border-radius:2px;text-transform:uppercase}

/* content */
.content{top:655px;height:290px;display:flex;gap:28px}
.welcome{flex:1}
.welcome h2{font-size:15px;color:var(--ink);font-weight:600;margin-bottom:8px}
.welcome p{color:var(--muted);margin-bottom:8px}
.welcome .more{color:var(--blue)}
.checks{list-style:none}
.checks li{display:flex;align-items:center;gap:5px;color:var(--muted);margin-bottom:2px}
.news{width:200px}
.news h2{font-size:15px;font-weight:600;margin-bottom:8px}
.news article{margin-bottom:10px}
.news h4{color:var(--orange);font-size:9.5px;font-weight:600}
.news p{color:var(--muted);font-size:8px}

/* footer */
.footer{position:absolute;left:0;top:960px;width:814px;height:210px;background:var(--footer)}
.footer-cols{position:absolute;left:82px;top:20px;width:654px;display:flex;gap:24px}
.footer-col h5{color:var(--white);font-size:12px;font-weight:600;margin-bottom:6px}
.footer-col li{list-style:none;color:var(--footer-text);font-size:8px;line-height:1.6}
.footer-map{width:110px;height:80px;border-radius:2px;background:linear-gradient(135deg,#cfd9c9,#e8e4d8 60%,#a9c3d8)}
.contact p{color:var(--footer-text);font-size:8px}
.social{display:flex;gap:4px;margin-top:6px}
.social span{width:14px;height:14px;border-radius:50%;background:var(--footer-text)}
.partners{position:absolute;left:82px;top:150px;display:flex;gap:18px}
.partners span{width:46px;height:20px;border-radius:2px;background:#3b4248}
.footer-bar{position:absolute;left:0;top:1170px;width:814px;height:30px;background:var(--footer-bar);color:var(--footer-text);font-size:7px;line-height:30px;padding-left:82px}
</style>
</head>
<body>
<div class="site">
  <header class="wrap header">
    <div class="brand"><span class="brand-name">Tendralwick Care</span></div>
    <div class="appointment"><small>Make an Appointment</small><strong>685.555.0142</strong></div>
  </header>

  <nav class="nav">
    <ul>
      <li class="active">HOME</li><li>ABOUT US</li><li>OUR SERVICES</li><li>RESOURCES</li><li>THE TEAM</li><li>CONTACT US</li>
    </ul>
  </nav>

  <section class="wrap hero">
    <div class="hero-photo" role="img" aria-label="Therapist examining a spine model with a patient"></div>
    <div class="hero-caption">
      <p>Duis tincidunt lectus quis dui</p>
      <h2>Spinal Code Injury Treatment</h2>
    </div>
    <div class="hero-dots"><span class="on"></span><span></span><span></span><span></span></div>
  </section>

  <section class="wrap features">
    <div class="feature">
      <div class="feature-photo" role="img" aria-label="Spine model on a blue background" style="background:linear-gradient(135deg,#3a7fc0,#a9cbe8)"></div>
      <h3>Spinal Code Treatment</h3>
      <p>Care plans built around each client, their goals and their family.</p>
      <span class="btn">Read more</span>
    </div>
    <div class="feature">
      <div class="feature-photo" role="img" aria-label="Group of care staff in uniform" style="background:linear-gradient(135deg,#d8dde2,#8fa6b8)"></div>
      <h3>The Team</h3>
      <p>Skilled nurses and support workers who bring warmth to every visit.</p>
      <span class="btn">Read more</span>
    </div>
    <div class="feature">
      <div class="feature-photo" role="img" aria-label="Smiling carer at work" style="background:linear-gradient(135deg,#e7d6cc,#b9a7a0)"></div>
      <h3>Join Our Team</h3>
      <p>We are looking for caring people to grow with us in the community.</p>
      <span class="btn">Read more</span>
    </div>
  </section>

  <section class="wrap content">
    <div class="welcome">
      <h2>Welcome to Tendralwick Care Mainpage</h2>
      <p>Tendralwick Care is a small team of care professionals committed to providing quality one to one care with heart. We bring years of experience supporting people with spinal cord injury to live well at home and in the community.</p>
      <p>Our nurses and support workers are trained in complex care and work closely with families, therapists and doctors. We take time to listen, plan together and adjust care as needs change, so every client feels safe, respected and in control of their day.</p>
      <p class="more">» Tendralwick Care provides</p>
      <ul class="checks">
        <li><svg width="9" height="9" viewBox="0 0 10 10"><circle cx="5" cy="5" r="5" fill="#2a7fc6"/><path d="M2.5 5.2l1.7 1.6 3.3-3.4" stroke="#fff" stroke-width="1.3" fill="none"/></svg>Professionally supported service and family based care</li>
        <li><svg width="9" height="9" viewBox="0 0 10 10"><circle cx="5" cy="5" r="5" fill="#2a7fc6"/><path d="M2.5 5.2l1.7 1.6 3.3-3.4" stroke="#fff" stroke-width="1.3" fill="none"/></svg>Regular specialist care for clients with SCI needs</li>
        <li><svg width="9" height="9" viewBox="0 0 10 10"><circle cx="5" cy="5" r="5" fill="#2a7fc6"/><path d="M2.5 5.2l1.7 1.6 3.3-3.4" stroke="#fff" stroke-width="1.3" fill="none"/></svg>Assistance with daily living tasks and community access</li>
        <li><svg width="9" height="9" viewBox="0 0 10 10"><circle cx="5" cy="5" r="5" fill="#2a7fc6"/><path d="M2.5 5.2l1.7 1.6 3.3-3.4" stroke="#fff" stroke-width="1.3" fill="none"/></svg>Tendralwick Care is available 24 hours, seven days per week</li>
      </ul>
    </div>
    <aside class="news">
      <h2>Latest News</h2>
      <article><h4>Spinal Cord Injury Forum</h4><p>Families and carers gathered to share stories, ideas and practical tips for better care.</p></article>
      <article><h4>Wheelchair rugby a family affair for mums and sons</h4><p>Local players showed skill and spirit as the whole community came out to cheer them on.</p></article>
      <article><h4>Work Skills Pays Forum</h4><p>A new program helps clients build confidence and skills for paid work in their area.</p></article>
    </aside>
  </section>

  <footer class="footer">
    <div class="footer-cols">
      <div class="footer-col"><h5>Quick Links</h5><ul><li>Home</li><li>About Us</li><li>Services</li><li>Our Team</li></ul></div>
      <div class="footer-col"><h5>Services</h5><ul><li>Quadriplegia</li><li>Tetraplegia</li><li>Spinal Code Injury</li><li>Physical Therapy</li></ul></div>
      <div class="footer-col"><h5>Resources</h5><ul><li>Blog Post</li><li>Latest News</li><li>Testimonials</li><li>Contact</li></ul></div>
      <div class="footer-map" role="img" aria-label="Street map of the clinic location"></div>
      <div class="footer-col contact"><h5>Contact Info</h5>
        <p>Tendralwick Care - Brenmoor<br>24 Larkfield Rd,<br>Brenmoor Victoria, 3981<br>(03) 5550 0190</p>
        <div class="social"><span></span><span></span><span></span><span></span></div>
      </div>
    </div>
    <div class="partners"><span></span><span></span><span></span><span></span><span></span></div>
  </footer>
  <div class="footer-bar">© 2014 Company Name. All rights reserved. Terms of Use</div>
</div>
</body>
</html>
```